SkyvornQ Business Cards and Stationary Design

Need a design for our business cards and stationary. I want to carry on the theme of the logo. I want the business cards to have a design on the back. I would like the business cards and the stationary to carry the same theme, design scheme, and branding

Target Market(s)

Airlines and Maintenance Facilities

Industry/Entity Type

Aviation

Contact Information for Business Card

Name
Position Title
Address: 4827 Trellis Hollow Road, Cedar Haven, Vermont, 34951
Office Number
Mobile Number
Email
Website

Font styles to use
Serif
Sans Serif

Colors

Designer to choose colors to be used in the design.

```html
<!DOCTYPE html>
<html lang="en">
<head>
<meta charset="utf-8">
<title>SkyvornQ Business Card</title>
<link rel="stylesheet" href="https://fonts.googleapis.com/css2?family=Open+Sans:wght@400;600;700;800&display=swap">
<style>
  :root {
    --navy: #0b2a55;
    --sky: #1e96d8;
    --ink: #3a3f47;
    --rule: #8a8f96;
    --paper: #ffffff;
    --backdrop: #2b2b2d;
  }
  * { margin: 0; padding: 0; box-sizing: border-box; }
  html, body { width: 1200px; height: 900px; overflow: hidden; }
  body {
    background: var(--backdrop);
    font-family: "Open Sans", Arial, sans-serif;
    position: relative;
  }
  .card {
    position: absolute;
    width: 620px;
    height: 354px;
    border-radius: 18px;
    overflow: hidden;
  }
  .card-front { left: 90px; top: 70px; background: var(--paper); }
  .card-back { left: 490px; top: 476px; background: var(--navy); }

  .front-shapes { position: absolute; inset: 0; }

  .front-brand {
    position: absolute;
    right: 40px;
    top: 30px;
    text-align: right;
  }
  .brand-circle {
    display: block;
    width: 58px; height: 58px;
    border: 5px solid var(--sky);
    border-radius: 50%;
    margin: 0 56px 10px auto;
  }
  .brand-name {
    font-weight: 800;
    font-size: 40px;
    letter-spacing: 5px;
    color: var(--navy);
    line-height: 1;
  }

  .address {
    position: absolute;
    right: 34px;
    top: 210px;
    text-align: right;
    font-size: 14px;
    line-height: 20px;
    color: var(--ink);
  }
  .front-web {
    position: absolute;
    right: 30px;
    top: 308px;
    font-size: 14px;
    color: var(--paper);
    letter-spacing: 0.5px;
  }

  .person {
    position: absolute;
    left: 32px;
    top: 166px;
  }
  .person-name {
    font-weight: 700;
    font-size: 20px;
    line-height: 26px;
    color: var(--navy);
    letter-spacing: 0.3px;
  }
  .person-title {
    font-size: 14px;
    line-height: 18px;
    color: var(--ink);
    margin-top: 12px;
  }
  .contacts {
    position: absolute;
    left: 34px;
    top: 240px;
    list-style: none;
    font-size: 14px;
    color: var(--ink);
  }
  .contacts li { display: flex; align-items: center; gap: 9px; height: 22px; }
  .contacts svg { width: 12px; height: 12px; fill: var(--navy); }

  .back-brand {
    position: absolute;
    left: 0; right: 0;
    top: 70px;
    text-align: center;
  }
  .back-brand .brand-circle {
    border-color: var(--paper);
    width: 78px; height: 78px;
    margin: 0 auto 16px;
  }
  .back-brand .brand-name {
    color: var(--paper);
    font-size: 52px;
    letter-spacing: 8px;
  }
  .back-web {
    position: absolute;
    left: 0; right: 0;
    top: 262px;
    display: flex;
    justify-content: center;
    align-items: center;
    gap: 16px;
    font-size: 15px;
    color: var(--paper);
  }
  .back-web .dash { width: 34px; height: 1px; background: var(--paper); opacity: 0.8; }
</style>
</head>
<body>

  <section class="card card-front" aria-label="Business card front">
    <svg class="front-shapes" width="620" height="354" viewBox="0 0 620 354">
      <line x1="30" y1="202" x2="590" y2="193" stroke="var(--rule)" stroke-width="1"/>
      <line x1="30" y1="202" x2="190" y2="199.5" stroke="var(--navy)" stroke-width="3"/>
      <path d="M0,336 L335,336 C366,336 368,282 404,278 L620,278" fill="none" stroke="var(--sky)" stroke-width="4"/>
      <path d="M0,354 L0,346 L342,346 C374,346 378,292 412,288 L620,288 L620,354 Z" fill="var(--navy)"/>
    </svg>

    <div class="front-brand">
      <span class="brand-circle"></span>
      <div class="brand-name">SKYVORNQ</div>
    </div>

    <div class="address">4827 Trellis Hollow Road,<br>Cedar Haven, Vermont, 34951</div>
    <div class="front-web">www.skyvornq.com</div>

    <div class="person">
      <div class="person-name">DANIEL MARSH</div>
      <div class="person-title">President</div>
    </div>

    <ul class="contacts">
      <li>
        <svg viewBox="0 0 24 24"><path d="M6.6 10.8a15 15 0 0 0 6.6 6.6l2.2-2.2c.3-.3.7-.4 1-.2 1.1.4 2.300.6 3.6.6.6 0 1 .4 1 1V20c0 .6-.4 1-1 1A17 17 0 0 1 3 4c0-.6.4-1 1-1h3.5c.6 0 1 .4 1 1 0 1.3.2 2.5.6 3.6.1.3 0 .7-.2 1z"/></svg>
        001 555 0148
      </li>
      <li>
        <svg viewBox="0 0 24 24"><path d="M7 1h10a2 2 0 0 1 2 2v18a2 2 0 0 1-2 2H7a2 2 0 0 1-2-2V3a2 2 0 0 1 2-2zm0 3v14h10V4z"/></svg>
        001 555 0148
      </li>
      <li>
        <svg viewBox="0 0 24 24"><path d="M2 5h20v14H2zm2 2v.5l8 5 8-5V7z"/></svg>
        info@skyvornq.com
      </li>
    </ul>
  </section>

  <section class="card card-back" aria-label="Business card back">
    <div class="back-brand">
      <span class="brand-circle"></span>
      <div class="brand-name">SKYVORNQ</div>
    </div>
    <div class="back-web">
      <span class="dash"></span>
      <span>www.skyvornq.com</span>
      <span class="dash"></span>
    </div>
  </section>

</body>
</html>
```